Business Card Design Project

Looking to update our business cards. We have a logo with our slogan. We are an IT firm so we wouldlike a modern look.

Industry/Entity Type

Business

```html
<!DOCTYPE html>
<html lang="en">
<head>
<meta charset="utf-8">
<title>Kelvora Business Cards</title>
<link rel="stylesheet" href="https://fonts.googleapis.com/css2?family=Jost:wght@500&family=Arimo:wght@400;700&display=swap">
<style>
  :root {
    --olive: #6b7f3e;
    --lime: #a9c23b;
    --white: #ffffff;
    --ink: #2b2b2b;
    --backdrop: #e9e7e2;
  }
  * { margin: 0; padding: 0; box-sizing: border-box; }
  html, body { width: 1200px; height: 699px; overflow: hidden; }
  body {
    background: var(--backdrop);
    position: relative;
    font-family: "Arimo", Arial, sans-serif;
  }
  .card {
    position: absolute;
    top: 200px;
    width: 520px;
    height: 300px;
    overflow: hidden;
    box-shadow: 0 6px 18px rgba(0,0,0,0.18);
  }
  .card--front { left: 50px; background: var(--white); }
  .card--back { left: 630px; background: var(--olive); }

  .front-wave { position: absolute; inset: 0; width: 520px; height: 300px; }

  .brand {
    position: absolute;
    display: flex;
    flex-direction: column;
    align-items: center;
    font-family: "Jost", "Futura", sans-serif;
    font-weight: 500;
  }
  .brand__name { display: flex; align-items: center; gap: 14px; letter-spacing: 10px; line-height: 1; }
  .brand__dot { width: 22px; height: 22px; border-radius: 50%; }
  .brand__tagline { letter-spacing: 5px; margin-top: 8px; }

  .card--front .brand { left: 0; width: 520px; top: 58px; color: var(--olive); }
  .card--front .brand__name { font-size: 58px; }
  .card--front .brand__dot { background: var(--olive); }
  .card--front .brand__tagline { font-size: 16px; color: var(--ink); }

  .contact {
    position: absolute;
    top: 200px;
    left: 160px;
    display: flex;
    color: var(--white);
  }
  .contact__person { text-align: right; padding-right: 14px; font-size: 13px; line-height: 1.35; }
  .contact__name { font-size: 20px; font-weight: 700; line-height: 1.2; }
  .contact__title { margin-bottom: 8px; }
  .contact__divider { width: 1px; background: var(--white); margin-top: 4px; height: 64px; }
  .contact__list { list-style: none; padding-left: 12px; font-size: 13px; line-height: 1.45; }
  .contact__list li { display: flex; align-items: center; gap: 7px; }
  .contact__list svg { width: 11px; height: 11px; fill: var(--white); flex: none; }

  .card--back .brand { left: 0; width: 520px; top: 86px; color: var(--white); }
  .card--back .brand__name { font-size: 62px; }
  .card--back .brand__dot { background: var(--white); }
  .card--back .brand__tagline { font-size: 17px; }
  .back-url {
    position: absolute;
    left: 0; width: 520px; bottom: 40px;
    text-align: center;
    color: var(--white);
    font-family: "Jost", "Futura", sans-serif;
    font-weight: 500;
    font-size: 24px;
    letter-spacing: 5px;
  }
</style>
</head>
<body>
  <section class="card card--front" aria-label="Business card front">
    <svg class="front-wave" viewBox="0 0 520 300" aria-hidden="true">
      <path d="M0,300 L0,238 Q210,150 520,168 L520,300 Z" fill="var(--olive)"/>
      <path d="M0,238 Q210,150 520,168 Q210,138 60,200 Z" fill="var(--lime)"/>
    </svg>
    <div class="brand">
      <div class="brand__name"><span>KELVORA</span><span class="brand__dot"></span></div>
      <div class="brand__tagline">MAKING TECH EASY</div>
    </div>
    <div class="contact">
      <div class="contact__person">
        <div class="contact__name">Your Name</div>
        <div class="contact__title">Title</div>
        <div>00, Complex name</div>
        <div>City, State 0042</div>
      </div>
      <div class="contact__divider"></div>
      <ul class="contact__list">
        <li><svg viewBox="0 0 12 12"><path d="M2,1 L4.5,1 L5.5,3.5 L4,4.8 Q5,7 7.2,8 L8.5,6.5 L11,7.5 L11,10 Q10,11 8.5,11 Q2,10 1,3.5 Q1,2 2,1 Z"/></svg>0987 654321</li>
        <li><svg viewBox="0 0 12 12"><rect x="3" y="0.5" width="6" height="11" rx="1"/></svg>0987 654321</li>
        <li><svg viewBox="0 0 12 12"><path d="M0.5,2 L11.5,2 L11.5,10 L0.5,10 Z M1.5,3 L6,6.5 L10.5,3 Z" fill-rule="evenodd"/></svg>info@kelvora.com</li>
        <li><svg viewBox="0 0 12 12"><circle cx="6" cy="6" r="5.5"/></svg>www.kelvora.com</li>
      </ul>
    </div>
  </section>

  <section class="card card--back" aria-label="Business card back">
    <div class="brand">
      <div class="brand__name"><span>KELVORA</span><span class="brand__dot"></span></div>
      <div class="brand__tagline">MAKING TECH EASY</div>
    </div>
    <div class="back-url">www.kelvora.com</div>
  </section>
</body>
</html>
```